Business Card Design

We are a manufacturing and distribution company with most of our customer base being supermarkets. We have established brand guidelines that are attached.

```html
<!DOCTYPE html>
<html lang="en">
<head>
<meta charset="utf-8">
<title>Velmora Business Card</title>
<link href="https://fonts.googleapis.com/css2?family=Montserrat:wght@700;800&family=Arimo:wght@400&display=swap" rel="stylesheet">
<style>
  :root {
    --brand-blue: #0a69ad;
    --brand-red: #e0262c;
    --ink: #1a1a1a;
    --paper: #ffffff;
    --stage: #d4d4d4;
  }
  * { margin: 0; padding: 0; box-sizing: border-box; }
  html, body { width: 1200px; height: 788px; overflow: hidden; }
  body {
    background: var(--stage);
    display: flex;
    align-items: center;
    justify-content: center;
    gap: 40px;
  }
  .card {
    width: 540px;
    height: 309px;
    position: relative;
    overflow: hidden;
    box-shadow: 0 6px 18px rgba(0,0,0,0.18);
  }
  .card-front { background: var(--paper); }
  .card-back {
    background: var(--brand-blue);
    display: flex;
    flex-direction: column;
    align-items: center;
    justify-content: center;
    gap: 22px;
  }
  .wordmark {
    font-family: "Montserrat", sans-serif;
    font-weight: 800;
    letter-spacing: 0.06em;
    line-height: 1;
  }
  .front-wordmark {
    position: absolute;
    left: 34px;
    top: 40px;
    font-size: 38px;
    color: var(--ink);
  }
  .person {
    position: absolute;
    left: 34px;
    top: 100px;
  }
  .person-name {
    font-family: "Montserrat", sans-serif;
    font-weight: 800;
    font-size: 19px;
    letter-spacing: 0.04em;
    line-height: 1.1;
  }
  .first-name { color: var(--brand-red); }
  .last-name { color: var(--brand-blue); }
  .person-title {
    font-family: "Arimo", sans-serif;
    font-size: 13px;
    color: var(--ink);
    margin-top: 2px;
  }
  .accent-bar {
    position: absolute;
    left: 0;
    top: 104px;
    width: 14px;
    height: 34px;
    background: var(--brand-red);
  }
  .address, .contacts {
    position: absolute;
    left: 34px;
    font-family: "Arimo", sans-serif;
    font-size: 12.5px;
    line-height: 1.35;
    color: var(--ink);
  }
  .address { top: 160px; }
  .contacts { top: 212px; list-style: none; }
  .contacts li { display: flex; align-items: center; gap: 7px; }
  .contacts svg { width: 11px; height: 11px; flex: none; }
  .front-mark {
    position: absolute;
    right: 44px;
    top: 112px;
    display: flex;
    align-items: center;
    gap: 12px;
  }
  .mark-square {
    width: 26px;
    height: 26px;
    background: var(--brand-red);
  }
  .front-mark .wordmark { font-size: 30px; color: var(--brand-blue); }
  .back-square {
    width: 40px;
    height: 40px;
    background: var(--brand-red);
  }
  .back-wordmark { font-size: 44px; color: var(--paper); }
</style>
</head>
<body>
  <section class="card card-front">
    <div class="wordmark front-wordmark">VELMORA</div>
    <span class="accent-bar"></span>
    <div class="person">
      <div class="person-name"><span class="first-name">DANIEL</span> <span class="last-name">HART</span></div>
      <div class="person-title">CEO/Founder</div>
    </div>
    <div class="address">2150 Kestrel Lane<br>Country Name, AB 40213</div>
    <ul class="contacts">
      <li><svg viewBox="0 0 12 12"><circle cx="6" cy="6" r="6" fill="#0a69ad"/><path d="M4 3.2l1 1.6-.6.6c.4.8 1 1.4 1.8 1.8l.6-.6 1.6 1-.5 1.1C5.9 8.7 3.3 6.1 3.1 4.1z" fill="#fff"/></svg>555-014-2298</li>
      <li><svg viewBox="0 0 12 12"><circle cx="6" cy="6" r="6" fill="#0a69ad"/><rect x="3" y="4" width="6" height="4.2" fill="#fff"/><path d="M3 4l3 2.3L9 4" stroke="#0a69ad" stroke-width=".7" fill="none"/></svg>info@velmora.com.au</li>
      <li><svg viewBox="0 0 12 12"><circle cx="6" cy="6" r="6" fill="#0a69ad"/><circle cx="6" cy="6" r="3" fill="none" stroke="#fff" stroke-width=".8"/><path d="M3 6h6M6 3v6" stroke="#fff" stroke-width=".7"/></svg>www.velmora.com.au</li>
    </ul>
    <div class="front-mark">
      <span class="mark-square"></span>
      <span class="wordmark">VELMORA</span>
    </div>
  </section>

  <section class="card card-back">
    <span class="back-square"></span>
    <div class="wordmark back-wordmark">VELMORA</div>
  </section>
</body>
</html>
```